Business Card Design Project

Business and Appointment Card for Medical Practice. On back of card we would like to have: blank line for patient name, Mon-Fri each with a check box next to the day, blank line for appointment date, blank line for appointment time, with option to circle am or pm.

Target Market(s)

Professional Business Associates, as well as function as patient appointment cards (on back side of card)

Industry/Entity Type

Business

Colors

Designer to choose colors to be used in the design.

```html
<!DOCTYPE html>
<html lang="en">
<head>
<meta charset="utf-8">
<title>Maple Grove Medical Associates – Business &amp; Appointment Card</title>
<link rel="stylesheet" href="https://fonts.googleapis.com/css2?family=Cinzel:wght@600&family=Open+Sans:wght@400;600&display=swap">
<style>
  :root {
    --green: #1d7a3e;
    --green-dark: #17652f;
    --red: #9b1c1f;
    --white: #ffffff;
    --grey-text: #6b6b6b;
    --faint: #e9e9e9;
    --backdrop: #e6e2dc;
  }
  * { box-sizing: border-box; margin: 0; padding: 0; }
  html, body { width: 1200px; height: 784px; overflow: hidden; }
  body {
    background: var(--backdrop);
    font-family: "Open Sans", Arial, sans-serif;
    position: relative;
  }
  .card {
    position: absolute;
    top: 237px;
    width: 540px;
    height: 309px;
    overflow: hidden;
    box-shadow: 0 6px 18px rgba(0,0,0,.18);
  }

  /* Appointment side */
  .card-back { left: 40px; background: linear-gradient(180deg, var(--green) 0%, var(--green-dark) 100%); color: var(--white); }
  .card-back .emblem-faint {
    position: absolute; left: 150px; top: 20px; width: 270px; height: 270px;
    border-radius: 50%; border: 4px solid rgba(255,255,255,.07); background: rgba(255,255,255,.04);
  }
  .appointment-title {
    position: absolute; left: 0; right: 0; top: 18px; text-align: center;
    color: var(--red); font-size: 17px; font-weight: 400;
  }
  .field-row { position: absolute; display: flex; align-items: center; font-size: 15px; }
  .field-label { width: 62px; text-align: right; padding-right: 8px; }
  .field-line { height: 22px; background: var(--white); }
  .row-top { left: 122px; top: 44px; }
  .row-top .field-line { width: 380px; }
  .row-name { left: 30px; top: 78px; }
  .row-date { left: 30px; top: 112px; }
  .row-time { left: 30px; top: 146px; }
  .row-name .field-line, .row-date .field-line, .row-time .field-line { width: 204px; }
  .weekdays { display: flex; gap: 6px; margin-left: 10px; font-size: 10px; align-items: center; }
  .weekday { display: flex; align-items: center; gap: 3px; }
  .check-box { width: 13px; height: 13px; background: var(--white); display: inline-block; }
  .meridiem { margin-left: 10px; font-size: 12px; }

  /* Business side */
  .card-front { left: 620px; background: var(--white); }
  .card-front .emblem-faint {
    position: absolute; right: -40px; top: 14px; width: 210px; height: 210px;
    border-radius: 50%; border: 5px solid var(--faint); background: rgba(0,0,0,.015);
  }
  .practice-name {
    position: absolute; left: 70px; top: 70px;
    font-family: "Cinzel", Georgia, serif; font-weight: 600; color: var(--red);
    font-size: 24px; line-height: 1.15; letter-spacing: .5px;
  }
  .contact-person { position: absolute; left: 70px; top: 150px; }
  .person-name { color: var(--red); font-weight: 600; font-size: 16px; }
  .person-role { color: var(--grey-text); font-size: 11px; margin-top: 1px; }
  .contact-list { position: absolute; left: 70px; top: 196px; list-style: none; color: var(--red); font-size: 12.5px; line-height: 18px; }
  .contact-list li { display: flex; align-items: center; gap: 6px; }
  .contact-list svg { width: 11px; height: 11px; fill: var(--red); flex: none; }
  .band-rule { position: absolute; left: 0; right: 0; bottom: 29px; height: 3px; background: var(--red); }
  .band { position: absolute; left: 0; right: 0; bottom: 4px; height: 25px; background: var(--green); }
  .band-foot { position: absolute; left: 0; right: 0; bottom: 0; height: 4px; background: var(--red); }
</style>
</head>
<body>

<section class="card card-back" aria-label="Appointment card">
  <div class="emblem-faint"></div>
  <h2 class="appointment-title">Appointment</h2>
  <div class="field-row row-top"><span class="field-line"></span></div>
  <div class="field-row row-name">
    <span class="field-label">Name :</span><span class="field-line"></span>
    <span class="weekdays">
      <span class="weekday">Mon<span class="check-box"></span></span>
      <span class="weekday">Tue<span class="check-box"></span></span>
      <span class="weekday">Wed<span class="check-box"></span></span>
      <span class="weekday">Thu<span class="check-box"></span></span>
      <span class="weekday">Fri<span class="check-box"></span></span>
    </span>
  </div>
  <div class="field-row row-date">
    <span class="field-label">Date :</span><span class="field-line"></span>
    <span class="meridiem">am / pm</span>
  </div>
  <div class="field-row row-time">
    <span class="field-label">Time :</span><span class="field-line"></span>
  </div>
</section>

<section class="card card-front" aria-label="Business card">
  <div class="emblem-faint"></div>
  <h1 class="practice-name">Maple Grove<br>Medical Associates</h1>
  <div class="contact-person">
    <p class="person-name">Daniel Hart</p>
    <p class="person-role">Manager</p>
  </div>
  <ul class="contact-list">
    <li><svg viewBox="0 0 24 24"><path d="M6.6 10.8a15 15 0 0 0 6.6 6.6l2.2-2.2c.3-.3.7-.4 1-.2 1.1.4 2.3.6 3.6.6.6 0 1 .4 1 1V20c0 .6-.4 1-1 1A17 17 0 0 1 3 4c0-.6.4-1 1-1h3.5c.6 0 1 .4 1 1 0 1.3.2 2.5.6 3.6.1.3 0 .7-.2 1z"/></svg>555-014-2290</li>
    <li><svg viewBox="0 0 24 24"><circle cx="12" cy="12" r="10"/><path d="M2 12h20M12 2c3 3 3 17 0 20M12 2c-3 3-3 17 0 20" stroke="#fff" stroke-width="1.6" fill="none"/></svg>www.maplegrovemed.com</li>
    <li><svg viewBox="0 0 24 24"><rect x="2" y="5" width="20" height="14" rx="2"/><path d="M3 6l9 7 9-7" stroke="#fff" stroke-width="1.8" fill="none"/></svg>info@maplegrovemed.com</li>
    <li><svg viewBox="0 0 24 24"><path d="M12 3 2 12h3v9h5v-6h4v6h5v-9h3z"/></svg>48 Linden Avenue Riverton</li>
  </ul>
  <div class="band-rule"></div>
  <div class="band"></div>
  <div class="band-foot"></div>
</section>

</body>
</html>
```